Flat bootstrap design for existing site

I'm looking for a modern flat design based around an existing logo. This has to be a custom design (no external templates), and implemented into a bootstrap framework.

The logo is attached as 2 versions - choose whichever you want, that flows better with whatever design you choose.

Added screenshots of the existing site (currently using the default bootstrap layouts). Please make your designs around those pages in the screenshots (i.e. the homepage only has the postal code input and the header). The active page has 3 screenshots, because I wanted to illustrate the other states that would be visible (in the table rows).

This is a moving/junk removal website, just for some context.

Here's some example websites (flat designs) that I like, just to give you an idea of what I'm after.

https://www.plimvora.com/
https://dacklow.com/
https://trevanu.com/
https://quobrintal.com/en/

Coding

Coded - Design and coding required

Number of Pages Required

5+ page

Colors

Designer to choose colors to be used in the design.

Requirements
Must have
• It must be a modern/simple flat design, that is built around the existing logo (attached).
• It has to be implemented using bootstrap.

```html
<!DOCTYPE html>
<html lang="en">
<head>
<meta charset="utf-8">
<title>Haulven – Junk Removal</title>
<link href="https://fonts.googleapis.com/css2?family=Mulish:wght@400;600;700;800&display=swap" rel="stylesheet">
<style>
  :root {
    --sky-top: #26b3e9;
    --sky-bottom: #41c4f1;
    --scene-tone: #1d9fd6;
    --white: #ffffff;
    --footer-bg: #e9e9e9;
    --footer-text: #7a7a7a;
    --placeholder: #8a8a8a;
  }
  * { box-sizing: border-box; margin: 0; padding: 0; }
  html, body { width: 1200px; height: 732px; overflow: hidden; }
  body { font-family: "Mulish", Arial, sans-serif; color: var(--white); }

  .hero {
    position: relative;
    width: 1200px;
    height: 665px;
    background: linear-gradient(180deg, var(--sky-top) 0%, var(--sky-bottom) 100%);
    overflow: hidden;
  }
  .city-scene {
    position: absolute;
    left: 100px;
    top: 180px;
    width: 1007px;
    height: 425px;
    background: linear-gradient(180deg, rgba(29,159,214,0) 0%, rgba(29,159,214,0.28) 45%, rgba(29,159,214,0.4) 88%, rgba(29,159,214,0) 100%);
  }

  .site-header {
    position: absolute;
    top: 0; left: 0; right: 0;
    height: 110px;
  }
  .brand {
    position: absolute;
    left: 156px;
    top: 34px;
    display: flex;
    align-items: center;
    gap: 10px;
    font-weight: 800;
    font-size: 40px;
    letter-spacing: 1px;
    line-height: 1;
    color: var(--white);
    text-decoration: none;
  }
  .brand-dot {
    width: 16px; height: 16px;
    border-radius: 50%;
    background: var(--white);
  }
  .main-nav {
    position: absolute;
    top: 44px;
    left: 532px;
    display: flex;
    gap: 37px;
  }
  .main-nav a {
    font-size: 16.5px;
    font-weight: 600;
    color: var(--white);
    text-decoration: none;
    letter-spacing: 0.2px;
    padding-bottom: 9px;
    border-bottom: 2px solid transparent;
  }
  .main-nav a.is-active { border-bottom-color: var(--white); }

  .booking {
    position: absolute;
    top: 228px;
    left: 0; right: 0;
    text-align: center;
  }
  .booking-title {
    font-size: 44px;
    font-weight: 700;
    letter-spacing: 0.3px;
    line-height: 1.1;
  }
  .postcode-input {
    display: block;
    margin: 41px auto 0;
    width: 577px;
    height: 55px;
    border: none;
    border-radius: 2px;
    padding: 0 17px;
    font-family: inherit;
    font-size: 16.5px;
    background: var(--white);
    box-shadow: 0 2px 6px rgba(0,0,0,0.12);
  }
  .postcode-input::placeholder { color: var(--placeholder); }
  .book-button {
    display: inline-block;
    margin-top: 27px;
    width: 183px;
    height: 55px;
    border: 3px solid var(--white);
    border-radius: 28px;
    background: transparent;
    color: var(--white);
    font-family: inherit;
    font-size: 20px;
    font-weight: 600;
  }

  .site-footer {
    height: 67px;
    background: var(--footer-bg);
    border-top: 1px solid #d6d6d6;
    display: flex;
    align-items: center;
    justify-content: center;
    font-size: 13.5px;
    color: var(--footer-text);
    gap: 8px;
  }
  .site-footer a { color: var(--footer-text); text-decoration: none; }
</style>
</head>
<body>
  <section class="hero">
    <div class="city-scene" role="img" aria-label="Line illustration of a city street with office towers, trees, recycling bins and a garbage truck with a worker"></div>

    <header class="site-header">
      <a class="brand" href="#"><span class="brand-dot"></span>HAULVEN</a>
      <nav class="main-nav">
        <a href="#">BOOK</a>
        <a href="#">HOW IT WORKS</a>
        <a href="#" class="is-active">BECOME A DRIVER</a>
        <a href="#">SIGN IN</a>
      </nav>
    </header>

    <form class="booking">
      <h1 class="booking-title">Need Junk Removed? Book Now</h1>
      <input class="postcode-input" type="text" placeholder="Type Postcode">
      <button class="book-button" type="button">Book Now</button>
    </form>
  </section>

  <footer class="site-footer">
    <span>© 2017 Company Name</span>
    <span>All right reserved</span>
    <a href="#">Term of Use</a>
  </footer>
</body>
</html>
```